Corvelle Meadow Organic Flower Farm, Farmer Florist

I am a flower grower and florist, so I do everything from the field to the vase. I want to include my website, phone, email and instagram

```html
<!DOCTYPE html>
<html lang="en">
<head>
<meta charset="utf-8">
<title>Corvelle Meadow – Business Card</title>
<link rel="stylesheet" href="https://fonts.googleapis.com/css2?family=Marcellus&family=Roboto:wght@400&display=swap">
<style>
  :root {
    --backdrop: #e4e4e4;
    --card-white: #f8f8f6;
    --bark: #655140;
    --wheat: #c99a52;
    --ink: #2c2c2c;
    --rule: #cfcfcf;
  }
  * { margin: 0; padding: 0; box-sizing: border-box; }
  html, body {
    width: 1200px; height: 930px; overflow: hidden;
    background: var(--backdrop);
  }
  .canvas { position: relative; width: 1200px; height: 930px; }

  .card {
    position: absolute;
    width: 560px; height: 320px;
    box-shadow: 0 6px 18px rgba(0,0,0,0.12);
  }

  /* Front side */
  .card--front { left: 80px; top: 500px; background: var(--card-white); }
  .front__tab {
    position: absolute; left: 0; top: 34px;
    width: 26px; height: 26px; background: var(--wheat);
  }
  .front__name {
    position: absolute; left: 40px; top: 34px;
    font-family: "Marcellus", serif; font-size: 22px; letter-spacing: 2px;
    color: var(--bark); line-height: 1;
  }
  .front__title {
    position: absolute; left: 40px; top: 62px;
    font-family: "Roboto", sans-serif; font-size: 14px; color: var(--ink);
  }
  .front__contacts {
    position: absolute; left: 18px; top: 96px; list-style: none;
    font-family: "Roboto", sans-serif; font-size: 14px; color: var(--ink);
  }
  .front__contacts li { display: flex; align-items: center; gap: 10px; height: 24px; }
  .front__contacts svg { width: 16px; height: 16px; }
  .front__rule {
    position: absolute; left: 220px; right: 40px; top: 160px;
    height: 1px; background: var(--rule);
  }
  .brand {
    position: absolute; display: flex; align-items: center; gap: 12px;
    font-family: "Marcellus", serif; letter-spacing: 4px; line-height: 1;
  }
  .brand__mark { display: block; }
  .front__brand { right: 40px; top: 68px; font-size: 34px; color: var(--bark); }
  .front__brand .brand__mark { width: 22px; height: 22px; background: var(--wheat); }
  .front__web {
    position: absolute; right: 40px; bottom: 30px;
    display: flex; align-items: center; gap: 14px;
    font-family: "Roboto", sans-serif; font-size: 15px; color: var(--ink);
  }
  .social-dot { width: 26px; height: 26px; border-radius: 50%; background: var(--wheat); }

  /* Back side */
  .card--back {
    left: 560px; top: 110px; background: var(--bark);
    display: flex; align-items: center; justify-content: center;
  }
  .back__brand { position: static; font-size: 40px; color: var(--card-white); }
  .back__brand .brand__mark { width: 24px; height: 24px; background: var(--card-white); }
</style>
</head>
<body>
<main class="canvas">

  <section class="card card--front" aria-label="Business card front">
    <span class="front__tab"></span>
    <h1 class="front__name">ELIAS MARLOWE</h1>
    <p class="front__title">Managing Director</p>
    <ul class="front__contacts">
      <li>
        <svg viewBox="0 0 16 16" aria-hidden="true">
          <rect x="0.75" y="0.75" width="14.5" height="14.5" rx="3" fill="none" stroke="#2c2c2c" stroke-width="1.2"/>
          <path d="M5.2 4c.5 0 .8.9 1 1.5.1.4-.5.8-.6 1.1.4.9 1 1.6 1.9 2 .3-.1.7-.7 1.1-.6.6.2 1.5.5 1.5 1 0 .8-.8 1.5-1.6 1.4C6.8 10.2 4.8 8.2 4.6 5.6 4.5 4.8 4.6 4 5.2 4z" fill="#2c2c2c"/>
        </svg>
        044-987 654 321
      </li>
      <li>
        <svg viewBox="0 0 16 16" aria-hidden="true">
          <rect x="0.5" y="3" width="15" height="10" fill="#2c2c2c"/>
          <path d="M0.5 3 L8 9 L15.5 3" fill="none" stroke="#f8f8f6" stroke-width="1.2"/>
        </svg>
        hello@corvellemeadow.com
      </li>
    </ul>
    <div class="front__rule"></div>
    <div class="brand front__brand">
      <span class="brand__mark"></span>CORVELLE
    </div>
    <div class="front__web">
      www.corvellemeadow.com
      <span class="social-dot" aria-label="Social profile"></span>
    </div>
  </section>

  <section class="card card--back" aria-label="Business card back">
    <div class="brand back__brand">
      <span class="brand__mark"></span>CORVELLE
    </div>
  </section>

</main>
</body>
</html>
```